Casino with the 'highest winning percentage' needs a stationery design

This is for a casino in Colombo, Sri Lanka and we need a stationery design for business card, letter head and envelope.

Should be very professional, simple and elegant without fancy fonts

Reason: Not fully satisfied with the designs. Need more designs.

Business

• 1. card deck symbol 'CLUBS' in red, or black

2. name in BLOCK CAPITAL LETTERS

3. Preferred font colours are black, white or red

4. Prefer 'professional /elegant' fonts
• SHOULD NOT HAVE ANY OTHER SYMBOL EXCEPT 'CLUBS'

DO NOT PREFER ITALIC FONTS

```html
<!DOCTYPE html>
<html lang="en">
<head>
<meta charset="utf-8">
<title>Marlowe's Entertainment – Business Card</title>
<link rel="stylesheet" href="https://fonts.googleapis.com/css2?family=Noto+Serif:wght@400;700&display=swap">
<style>
  :root {
    --red: #d62e3a;
    --black: #000000;
    --ink: #1a1a1a;
    --white: #ffffff;
    --backdrop: #e9e6e1;
    --rule: #cfcfcf;
  }
  * { margin: 0; padding: 0; box-sizing: border-box; }
  html, body { width: 1200px; height: 999px; overflow: hidden; }
  body {
    background: var(--backdrop);
    font-family: "Noto Serif", Georgia, serif;
    position: relative;
  }
  .card {
    position: absolute;
    width: 793px;
    height: 453px;
  }
  .card--front {
    left: 49px; top: 29px;
    background: var(--white);
    border: 1px solid #555;
  }
  .card--back {
    left: 381px; top: 506px;
    background: var(--black);
  }
  .brand-mark {
    position: absolute;
    border-radius: 50%;
    background: var(--red);
  }
  .card--front .brand-mark { left: 155px; top: 60px; width: 110px; height: 110px; }
  .card--back .brand-mark { left: 111px; top: 152px; width: 136px; height: 136px; }
  .brand-name {
    position: absolute;
    font-weight: 700;
    text-transform: uppercase;
    line-height: 1.3;
  }
  .card--front .brand-name { left: 302px; top: 62px; font-size: 42px; color: var(--black); }
  .card--back .brand-name { left: 278px; top: 163px; font-size: 46px; color: var(--white); }

  .rule { position: absolute; left: 0; right: 0; height: 3px; background: var(--black); }
  .rule--top { top: 221px; }
  .rule--bottom { top: 275px; }
  .tagline-band {
    position: absolute; left: 0; right: 0; top: 228px; height: 42px;
    background: var(--red);
    color: var(--white);
    font-weight: 700;
    font-size: 23px;
    letter-spacing: 2.6px;
    line-height: 42px;
    padding-left: 102px;
  }
  .company {
    position: absolute; right: 411px; top: 305px;
    text-align: right;
  }
  .company__name { color: var(--red); font-weight: 700; font-size: 25px; line-height: 1.2; margin-bottom: 6px; }
  .company__address { font-style: normal; color: var(--ink); font-size: 19px; line-height: 26px; }
  .divider { position: absolute; left: 406px; top: 305px; width: 1px; height: 127px; background: var(--rule); }
  .contacts { position: absolute; left: 427px; top: 302px; list-style: none; }
  .contacts li {
    display: flex; align-items: center; gap: 9px;
    height: 30px; font-size: 19px; color: var(--ink);
  }
  .contacts svg { width: 17px; height: 17px; flex: none; }
  .website {
    position: absolute; left: 0; right: 0; top: 370px;
    text-align: center; color: var(--white);
    font-size: 25px; letter-spacing: 6.5px;
  }
</style>
</head>
<body>
  <section class="card card--front">
    <span class="brand-mark"></span>
    <h1 class="brand-name">Marlowe's<br>Entertainment</h1>
    <div class="rule rule--top"></div>
    <p class="tagline-band">Highest Winning Percentage In The World</p>
    <div class="rule rule--bottom"></div>
    <div class="company">
      <p class="company__name">MARLOWE'S LIMITED</p>
      <address class="company__address">18, Lotus Garden Mawatha<br>Colombo 01000<br>Sri Lanka</address>
    </div>
    <div class="divider"></div>
    <ul class="contacts">
      <li><svg viewBox="0 0 20 20" aria-hidden="true"><circle cx="10" cy="10" r="8.5" fill="none" stroke="#d62e3a" stroke-width="1.6"/><path d="M7 5.5c-1 1-1 3 1 5.5s4.5 3.5 5.5 2.5l-1.5-1.8-1.5.8c-1-.5-2.3-2-2.6-3l1-1.2z" fill="#d62e3a"/></svg>+ 94 11 2000150</li>
      <li><svg viewBox="0 0 20 20" aria-hidden="true"><rect x="5" y="2" width="10" height="16" rx="1.5" fill="#d62e3a"/><rect x="7" y="4" width="6" height="4" fill="#fff"/><g fill="#fff"><rect x="7" y="10" width="1.5" height="1.5"/><rect x="9.3" y="10" width="1.5" height="1.5"/><rect x="11.5" y="10" width="1.5" height="1.5"/><rect x="7" y="13" width="1.5" height="1.5"/><rect x="9.3" y="13" width="1.5" height="1.5"/><rect x="11.5" y="13" width="1.5" height="1.5"/></g></svg>+ 94 77 0000000</li>
      <li><svg viewBox="0 0 20 20" aria-hidden="true"><rect x="6" y="3" width="8" height="5" fill="#d62e3a"/><rect x="2" y="8" width="16" height="8" rx="1.5" fill="#d62e3a"/><rect x="5" y="10.5" width="10" height="1.5" fill="#fff"/></svg>+ 94 11 0000000</li>
      <li><svg viewBox="0 0 20 20" aria-hidden="true"><path d="M2 8l8-5 8 5v9H2z" fill="#d62e3a"/><path d="M2 8l8 5 8-5" fill="none" stroke="#fff" stroke-width="1.4"/></svg>info@marlowescolombo.com</li>
    </ul>
  </section>

  <section class="card card--back">
    <span class="brand-mark"></span>
    <h2 class="brand-name">Marlowe's<br>Entertainment</h2>
    <p class="website">www.marlowescolombo.com</p>
  </section>
</body>
</html>
```